Coastline Premier Retreats Business Card Design

Design a business card for Coastline Premier Retreats. Look at the website for colors and reference. Card should have logo, name, title, office number, mobile number, email, URL and a tagline like, "Luxury Hotel & Resort Email Marketing" (This might change).

https://www.coastlinepremierretreats.example

The rest I will leave up to your imagination.

Contact Information for Business Card

Logo, name, title, office number, mobile number, email, URL and a tagline like, "Luxury Hotel & Resort Email Marketing" (This might change).

```html
<!DOCTYPE html>
<html lang="en">
<head>
<meta charset="utf-8">
<title>Coastline Premier Retreats – Business Card</title>
<link rel="stylesheet" href="https://fonts.googleapis.com/css2?family=Arimo:wght@400;700&family=Montserrat:wght@400&display=swap">
<style>
  :root {
    --stage: #0e0e0e;
    --card: #1b1b1b;
    --card-back: #171717;
    --orange: #e8731a;
    --white: #f2f2f2;
  }
  * { margin: 0; padding: 0; box-sizing: border-box; }
  html, body { width: 1200px; height: 1059px; overflow: hidden; background: var(--stage); }
  body { position: relative; font-family: "Arimo", Arial, sans-serif; color: var(--white); }

  .card { position: absolute; }
  .card-front { left: 257px; top: 90px; width: 687px; height: 389px; background: var(--card); }
  .card-back { left: 254px; top: 547px; width: 693px; height: 393px; background: var(--card-back); }

  /* front frame with gap for tagline */
  .frame {
    position: absolute; left: 22px; top: 21px; right: 22px; bottom: 32px;
    border: 2px solid var(--orange); border-bottom: none;
  }
  .frame-bottom { position: absolute; bottom: 32px; height: 2px; background: var(--orange); }
  .frame-bottom.left { left: 22px; width: 156px; }
  .frame-bottom.right { right: 22px; width: 153px; }
  .tagline {
    position: absolute; left: 0; right: 0; bottom: 25px; text-align: center;
    font-size: 17.5px; color: var(--white);
  }

  .brand { position: absolute; display: flex; align-items: center; }
  .brand-mark { background: var(--orange); flex: none; }
  .brand-name { font-weight: 700; text-transform: uppercase; color: var(--white); line-height: 1.1; }

  .card-front .brand { left: 56px; top: 169px; gap: 12px; }
  .card-front .brand-mark { width: 14px; height: 14px; }
  .card-front .brand-name { font-size: 21px; letter-spacing: 1px; }

  .card-back .brand { left: 0; right: 0; top: 150px; justify-content: center; gap: 20px; }
  .card-back .brand-mark { width: 24px; height: 24px; }
  .card-back .brand-name { font-size: 40px; letter-spacing: 2px; }

  .divider { position: absolute; left: 349px; top: 99px; width: 1px; height: 190px; background: var(--orange); }

  .details { position: absolute; left: 378px; top: 95px; }
  .person-name { font-size: 29px; font-weight: 700; color: var(--orange); line-height: 1; letter-spacing: 0.5px; }
  .person-title { font-family: "Montserrat", Arial, sans-serif; font-size: 15.5px; margin-top: 3px; }
  .address { font-size: 16px; line-height: 21px; margin-top: 16px; }
  .contacts { list-style: none; margin-top: 11px; }
  .contacts li { display: flex; align-items: center; gap: 7px; font-size: 15px; line-height: 21.5px; white-space: nowrap; }
  .contacts svg { width: 12px; height: 12px; flex: none; fill: var(--orange); }
  .contacts li.long { font-size: 14px; }
</style>
</head>
<body>

<section class="card card-front" aria-label="Business card front">
  <div class="frame"></div>
  <div class="frame-bottom left"></div>
  <div class="frame-bottom right"></div>
  <p class="tagline">Luxury Hotel &amp; Resort Email Marketing</p>

  <div class="brand">
    <span class="brand-mark"></span>
    <span class="brand-name">Coastline Premier<br>Retreats</span>
  </div>

  <div class="divider"></div>

  <div class="details">
    <h1 class="person-name">MARCUS HALE</h1>
    <p class="person-title">CEO/Founder</p>
    <p class="address">Po Box, 48 B Harbor Rd<br>North America, AB 10420</p>
    <ul class="contacts">
      <li>
        <svg viewBox="0 0 12 12"><path d="M3 0h6a1 1 0 0 1 1 1v10a1 1 0 0 1-1 1H3a1 1 0 0 1-1-1V1a1 1 0 0 1 1-1zm0.5 1.5v7.5h5V1.5zM6 9.6a.7.7 0 1 0 0 1.4.7.7 0 0 0 0-1.4z"/></svg>
        555.014.2000
      </li>
      <li>
        <svg viewBox="0 0 12 12"><path d="M0 4c0-2 2.5-3 6-3s6 1 6 3v1H9V3.8H3V5H0zM2.5 6h7l1.5 5H1z"/></svg>
        +34 600 000 147
      </li>
      <li class="long">
        <svg viewBox="0 0 12 12"><path d="M0 5l6-4 6 4v7H0zM1.2 5.6v5.2l3.6-2.6zm9.6 0L7.2 8.2l3.6 2.6zM2 11h8L6 8z"/></svg>
        info@coastlinepremierretreats.example
      </li>
      <li class="long">
        <svg viewBox="0 0 12 12"><path d="M6 0a6 6 0 1 1 0 12A6 6 0 0 1 6 0zm-2 2.5 1 1.5-1 1.5 1.5 1 0 2 1.5-1 .5-2 1.5-.5-.5-2L6 1.5z"/></svg>
        www.coastlinepremierretreats.example
      </li>
    </ul>
  </div>
</section>

<section class="card card-back" aria-label="Business card back">
  <div class="brand">
    <span class="brand-mark"></span>
    <span class="brand-name">Coastline Premier<br>Retreats</span>
  </div>
</section>

</body>
</html>
```